Meridale Nutrition needs Stationary and a business card

We would like to use our current logo. The text can be moved around as needed. The stationary needs to be a 'first page' where the logo is more prominent to be impressive on higher quality paper and a second page where the logo is more subtle where there will be much more information on the page. There are 2 clinic locations which will need include name, address, phone number, fax number, web address. The business card should be single sided and contain this information also.
The design must be contemporary and sophisticated as this is a science based diet run out of a medical clinic.

Target Market(s)

People wanting to lose weight, athletes looking to optimise performance, people with arthritis or fighting cancer

Industry/Entity Type

Business

Contact Information for Business Card

must use the logo. I have attached an example card with the practice details on it. there must be space for the doctors name. Also the website www.meridalenutrition.com.au

Requirements
Must have
• the logo, the business adresses and phone numbers, the website, the doctors name and qualifications
Nice to have
• some creativity
Should not have
• Do not simply reproduce the existing card please

```html
<!DOCTYPE html>
<html lang="en">
<head>
<meta charset="utf-8">
<title>Meridale Nutrition – Stationery</title>
<link href="https://fonts.googleapis.com/css2?family=Jost:wght@400;500&family=Pathway+Gothic+One&display=swap" rel="stylesheet">
<style>
  :root {
    --backdrop: #9b9ca0;
    --paper: #ffffff;
    --brand-blue: #2f6fae;
    --sky-blue: #3fb3e6;
    --ink: #3a3d42;
    --soft-grey: #d6dbe3;
    --wash: #e4f1fb;
    --rule: #cfe8f6;
  }
  * { box-sizing: border-box; margin: 0; padding: 0; }
  html, body { width: 1200px; height: 1200px; overflow: hidden; }
  body { background: var(--backdrop); position: relative; font-family: "Pathway Gothic One", sans-serif; color: var(--ink); }

  .sheet {
    position: absolute; top: 110px; width: 500px; height: 707px;
    background: var(--paper); box-shadow: 0 4px 14px rgba(0,0,0,.25); overflow: hidden;
  }
  .sheet--continuation { left: 70px; }
  .sheet--first { left: 630px; }

  .sheet-wash {
    position: absolute; left: 0; right: 0; bottom: 0; height: 380px;
    background: linear-gradient(to bottom, rgba(228,241,251,0), var(--wash));
  }
  .sheet-footer {
    position: absolute; left: 0; right: 0; bottom: 22px; text-align: center;
    font-size: 14px; letter-spacing: .6px; color: var(--brand-blue);
  }

  /* continuation page */
  .sheet-wordmark {
    position: absolute; left: 30px; bottom: 40px;
    writing-mode: vertical-rl; transform: rotate(180deg);
    font-family: "Jost", sans-serif; font-weight: 500; font-size: 52px;
    letter-spacing: 1px; color: var(--soft-grey); white-space: nowrap;
  }
  .sheet-rule {
    position: absolute; left: 96px; top: 60px; width: 3px; height: 330px; background: var(--rule);
  }

  /* first page */
  .letterhead { position: absolute; top: 30px; left: 22px; right: 18px; display: flex; align-items: flex-start; gap: 14px; }
  .brand { display: flex; flex-direction: column; align-items: center; width: 160px; flex: none; }
  .brand-dot { width: 96px; height: 96px; border-radius: 50%; background: var(--sky-blue); }
  .brand-name {
    margin-top: 10px; font-family: "Jost", sans-serif; font-weight: 500; font-size: 16px;
    letter-spacing: .4px; color: var(--brand-blue); text-transform: uppercase; white-space: nowrap;
  }
  .divider { width: 1px; height: 150px; background: var(--ink); opacity: .6; flex: none; }
  .clinics { font-size: 14px; line-height: 1.25; white-space: nowrap; }
  .clinic + .clinic { margin-top: 8px; }
  .clinic-name, .clinic-accent { color: var(--brand-blue); }

  /* business card */
  .card {
    position: absolute; left: 375px; top: 880px; width: 450px; height: 258px;
    background: linear-gradient(100deg, #ffffff 55%, #e6f3fb 100%);
    box-shadow: 0 4px 12px rgba(0,0,0,.28); overflow: hidden;
  }
  .card-band { position: absolute; right: 0; top: 0; height: 100%; width: 130px; }
  .card-brand { position: absolute; left: 18px; top: 22px; display: flex; flex-direction: column; align-items: center; width: 130px; }
  .card-brand .brand-dot { width: 52px; height: 52px; }
  .card-brand .brand-name { font-size: 11px; margin-top: 6px; }
  .card-person { position: absolute; left: 152px; top: 26px; white-space: nowrap; }
  .card-person-name { font-family: "Jost", sans-serif; font-weight: 400; font-size: 22px; color: var(--brand-blue); }
  .card-person-quals { font-size: 10px; letter-spacing: .2px; margin-top: 2px; }
  .card-person-role { font-size: 12.5px; margin-top: 2px; }
  .card-person-web { font-size: 12.5px; margin-top: 2px; color: var(--brand-blue); }
  .card-clinics { position: absolute; left: 24px; top: 118px; font-size: 11.5px; line-height: 14px; white-space: nowrap; }
  .card-clinics .clinic + .clinic { margin-top: 8px; }
</style>
</head>
<body>

  <section class="sheet sheet--continuation" aria-label="Letterhead continuation page">
    <div class="sheet-wash"></div>
    <div class="sheet-rule"></div>
    <div class="sheet-wordmark">MERIDALE NUTRITION</div>
    <div class="sheet-footer">www.meridalenutrition.com.au</div>
  </section>

  <section class="sheet sheet--first" aria-label="Letterhead first page">
    <div class="sheet-wash" role="img" aria-label="Faint repeating brand pattern fading into the lower page"></div>
    <header class="letterhead">
      <div class="brand">
        <div class="brand-dot"></div>
        <div class="brand-name">Meridale Nutrition</div>
      </div>
      <div class="divider"></div>
      <div class="clinics">
        <div class="clinic">
          <div class="clinic-name">Ashgrove</div>
          <div>21-23 Harbour Street, Ashgrove NSW 2131</div>
          <div><span class="clinic-accent">T.</span> 02 9410 3825 | <span class="clinic-accent">F.</span> 02 9410 3826</div>
          <div><span class="clinic-accent">Shoulder &amp; Elbow</span> www.elliotmarsh.com.au</div>
        </div>
        <div class="clinic">
          <div class="clinic-name">Linfield</div>
          <div>88 Carlisle Road, Linfield NSW 2040</div>
          <div><span class="clinic-accent">T.</span> 02 9488 1270 | <span class="clinic-accent">F.</span> 02 9488 1271</div>
          <div><span class="clinic-accent">Knee Surgery</span> www.jointclinic.com.au</div>
        </div>
      </div>
    </header>
    <div class="sheet-footer">www.meridalenutrition.com.au</div>
  </section>

  <section class="card" aria-label="Business card">
    <svg class="card-band" viewBox="0 0 130 258" preserveAspectRatio="none" role="img" aria-label="Blue patterned band along the right edge">
      <defs>
        <linearGradient id="bandFill" x1="0" y1="0" x2="1" y2="1">
          <stop offset="0" stop-color="#4fbdeb"/>
          <stop offset="1" stop-color="#2a9fd8"/>
        </linearGradient>
      </defs>
      <path d="M30 0 C 0 60, 40 120, 80 160 C 110 190, 110 230, 118 258 L130 258 L130 0 Z" fill="url(#bandFill)"/>
      <path d="M30 0 C 0 60, 40 120, 80 160 C 110 190, 110 230, 118 258" fill="none" stroke="#2f6fae" stroke-width="3"/>
    </svg>
    <div class="card-brand">
      <div class="brand-dot"></div>
      <div class="brand-name">Meridale Nutrition</div>
    </div>
    <div class="card-person">
      <div class="card-person-name">Dr Elliot Marsh</div>
      <div class="card-person-quals">MBBS (NSW) MBiomedE FRACS (Ortho) FAOrthA</div>
      <div class="card-person-role">Orthopaedic Surgeon</div>
      <div class="card-person-web">www.meridalenutrition.com.au</div>
    </div>
    <div class="card-clinics">
      <div class="clinic">
        <div class="clinic-name">Ashgrove</div>
        <div>21-23 Harbour Street, Ashgrove NSW 2131</div>
        <div>T. 02 9410 3825 | F. 02 9410 3826</div>
        <div><span class="clinic-accent">Shoulder &amp; Elbow</span> www.elliotmarsh.com.au</div>
      </div>
      <div class="clinic">
        <div class="clinic-name">Linfield</div>
        <div>88 Carlisle Road, Linfield NSW 2040</div>
        <div>T. 02 9488 1270 | F. 02 9488 1271</div>
        <div><span class="clinic-accent">Knee Surgery</span> www.jointclinic.com.au</div>
      </div>
    </div>
  </section>

</body>
</html>
```